Custom Manufacturing Company square space website design

I own a custom manufacturing company that uses precision cutting technology to manufacture project components over a couple industries. We have an industrial CNC router and state of the art edge bander and cut a lot of cabinetry components for cabinet shops, builders, closet companies, ect. We offer design and assembly for any cabinetry or can build cabinets to spec. We also cut components for other industries out of wood, plastics, acryclics, ect. We offer design engineering services, product development protype services. we have a 3D printer farm. We want our communicate trust, dependability, and the value we place on client relationships.

We essentially want a credibility website. Landing page and drops downs for services we offer, capabilites, about us, contact

```html
<!DOCTYPE html>
<html lang="en">
<head>
<meta charset="utf-8">
<title>Lakeside CNC</title>
<link href="https://fonts.googleapis.com/css2?family=Orbitron:wght@600;700&family=Raleway:wght@400;500&display=swap" rel="stylesheet">
<style>
:root{
  --ink:#141414;
  --night:#151515;
  --footer:#2a2a2a;
  --paper:#ffffff;
  --mist:#f1f1f2;
  --field:#efeff1;
  --line:#555555;
  --muted:#8a8a8a;
  --sand-1:#d9d2c8;
  --sand-2:#c9bfb1;
  --wood:#c7ab7a;
  --steel:#2c3a5a;
}
*{box-sizing:border-box;margin:0;padding:0}
html,body{width:1200px;height:3758px;overflow:hidden}
body{position:relative;background:var(--paper);font-family:"Raleway",sans-serif;color:var(--ink)}
.abs{position:absolute}
.heading{font-family:"Orbitron",sans-serif;font-weight:700;letter-spacing:1px;text-transform:uppercase}
.pill{position:absolute;display:flex;align-items:center;justify-content:center;border:1.5px solid var(--ink);border-radius:22px;font-size:17px;text-transform:uppercase;color:var(--ink);background:transparent}
.pill.light{border-color:#fff;color:#fff}

/* header */
.site-header{left:0;top:0;width:1200px;height:117px;background:var(--ink)}
.brand{display:flex;align-items:center;gap:10px;color:#fff;font-family:"Orbitron",sans-serif;font-weight:600;font-size:15px;letter-spacing:2px}
.brand-square{width:14px;height:14px;border:2px solid #fff}
.site-header .brand{position:absolute;left:115px;top:46px}
.main-nav{position:absolute;top:48px;font-size:15px;color:#fff}

/* hero */
.hero-photo{left:0;top:117px;width:1200px;height:640px;background:linear-gradient(180deg,var(--sand-1) 0%,var(--sand-2) 55%,var(--wood) 75%,#b8a996 100%)}
.hero-title{left:0;top:244px;width:1200px;text-align:center;font-size:44px;line-height:52px;color:var(--ink)}

/* about */
.about-photo{left:114px;top:884px;width:481px;height:342px;background:linear-gradient(135deg,#8a7f78 0%,#cfc3b4 45%,#5b4e48 70%,#d7c6a8 100%)}
.section-title{font-size:30px}
.about-text{left:625px;top:937px;width:464px;font-size:16.5px;line-height:29px;text-align:justify;color:#222}

/* services */
.services-text{left:100px;top:1530px;width:1000px;text-align:center;font-size:16.5px;line-height:29px;color:#222}
.service-photo{top:1650px;width:282px;height:460px}
.service-label{top:2136px;width:282px;text-align:center;font-family:"Orbitron",sans-serif;font-weight:600;font-size:19px;letter-spacing:1px}

/* capabilities */
.cap-title{left:0;top:2432px;width:1200px;text-align:center;font-size:30px;color:#fff}
.cap-text{left:100px;top:2500px;width:1000px;text-align:center;font-size:16.5px;line-height:29px;color:#fff}

/* contact */
.contact-title{left:114px;top:2910px;font-size:30px;color:#fff}
.contact-text{left:114px;top:2972px;width:430px;font-size:16.5px;line-height:29px;color:#fff}
.social{display:flex;gap:13px}
.social span{width:30px;height:30px;border-radius:50%;background:#fff}
.field{left:625px;width:422px;background:var(--field);border-radius:5px;font-size:14px;color:var(--muted);padding:14px 24px}

/* footer */
.site-footer{left:0;top:3356px;width:1200px;height:402px;background:var(--footer)}
.footer-nav{top:3553px;font-size:15px;color:#fff}
.footer-rule{left:114px;top:3673px;width:974px;height:1px;background:#777}
.copyright{left:0;top:3704px;width:1200px;text-align:center;font-size:14px;color:#fff}
</style>
</head>
<body>

<header class="abs site-header">
  <div class="brand"><span class="brand-square"></span>LAKESIDE CNC</div>
  <nav>
    <span class="main-nav" style="left:548px">Home</span>
    <span class="main-nav" style="left:637px">Services we offer</span>
    <span class="main-nav" style="left:799px">Capabilities</span>
    <span class="main-nav" style="left:926px">About us</span>
    <span class="main-nav" style="left:1034px">Contact</span>
  </nav>
</header>

<section>
  <div class="abs hero-photo" role="img" aria-label="Living room with a slatted wooden sideboard and a woven lounge chair against a plaster wall"></div>
  <svg class="abs" style="left:0;top:660px" width="1200" height="100" viewBox="0 0 1200 100" aria-hidden="true">
    <polygon points="0,95 600,12 1200,95 1200,100 0,100" fill="#141414"/>
    <polygon points="0,100 600,32 1200,100" fill="#ffffff"/>
  </svg>
  <h1 class="abs heading hero-title">Welcome to<br>Lakeside CNC</h1>
  <a class="pill" style="left:520px;top:373px;width:160px;height:42px">Contact us</a>
</section>

<section>
  <div class="abs about-photo" role="img" aria-label="Close-up of a CNC router spindle cutting into a wooden board"></div>
  <h2 class="abs heading section-title" style="left:625px;top:880px">About us</h2>
  <p class="abs about-text">Lorem ipsum dolor sit amet, consectetur adipiscing elit, sed do eiusmod tempor incididunt ut labore et dolore magna aliqua. Quis ipsum suspendisse ultrices gravida. Risus commodo viverra maecenas accumsan lacus vel facilisis. Lorem ipsum dolor sit amet, consectetur adipiscing elit, sed do eiusmod tempor incididunt ut labore et dolore magna aliqua. Quis ipsum suspendisse ultrices gravida. Risus commodo viverra maecenas accumsan lacus vel facilisis.</p>
  <a class="pill" style="left:625px;top:1193px;width:161px;height:42px">Read more</a>
</section>

<section>
  <svg class="abs" style="left:0;top:1328px" width="1200" height="1010" viewBox="0 0 1200 1010" aria-hidden="true">
    <polygon points="0,76 1200,0 1200,1010 0,1010" fill="#f1f1f2"/>
    <polygon points="0,45 350,75 0,106" fill="#141414"/>
  </svg>
  <h2 class="abs heading section-title" style="left:0;top:1465px;width:1200px;text-align:center">Services we offer</h2>
  <p class="abs services-text">Lorem ipsum dolor sit amet, consectetur adipiscing elit, sed do eiusmod tempor incididunt ut labore et dolore magna aliqua.<br>Quis ipsum suspendisse ultrices gravida. Risus commodo viverra maecenas accumsan lacus vel facilisis.</p>

  <div class="abs service-photo" style="left:112px;background:linear-gradient(180deg,#9aa39e 0%,#4f8a4a 45%,#3b3f44 70%,#d8c6a6 100%)" role="img" aria-label="Woodworker feeding a board through a green cabinet-shop machine"></div>
  <div class="abs service-photo" style="left:459px;background:linear-gradient(160deg,#3f6aa0 0%,#9fb8cf 40%,#2c4f7a 70%,#1f3555 100%)" role="img" aria-label="Metal lathe turret with cutting tools"></div>
  <div class="abs service-photo" style="left:806px;background:linear-gradient(180deg,#d8d8d6 0%,#c9c9c5 45%,#8c8c88 75%,#6d6d6b 100%)" role="img" aria-label="Flatbed cutting machine in a bright workshop"></div>

  <div class="abs service-label" style="left:98px">Cabinet shops</div>
  <div class="abs service-label" style="left:459px">Builders</div>
  <div class="abs service-label" style="left:806px">Closet companies</div>

  <a class="pill" style="left:520px;top:2223px;width:160px;height:42px">View more</a>
</section>

<section>
  <svg class="abs" style="left:0;top:2345px" width="1200" height="1011" viewBox="0 0 1200 1011" aria-hidden="true">
    <defs>
      <linearGradient id="workshop-tone" x1="0" y1="0" x2="1" y2="1">
        <stop offset="0" stop-color="#2e3c62"/>
        <stop offset="0.5" stop-color="#4c5670"/>
        <stop offset="1" stop-color="#2a3350"/>
      </linearGradient>
    </defs>
    <rect x="0" y="0" width="1200" height="1011" fill="#151515"/>
    <polygon points="0,0 1200,0 1200,425 0,381" fill="url(#workshop-tone)" role="img" aria-label="Machinist operating equipment in a workshop"/>
    <polygon points="1200,425 700,455 1200,491" fill="#ffffff"/>
  </svg>
  <h2 class="abs heading cap-title">Capabalities</h2>
  <p class="abs cap-text">Lorem ipsum dolor sit amet, consectetur adipiscing elit, sed do eiusmod tempor incididunt ut labore et dolore magna aliqua. Quis ipsum suspendisse ultrices gravida. Risus commodo viverra maecenas accumsan lacus vel facilisis. Lorem ipsum dolor sit amet, consectetur adipiscing elit, sed do eiusmod tempor incididunt ut labore et dolore magna aliqua. Quis ipsum suspendisse ultrices gravida. Risus commodo viverra maecenas accumsan lacus vel facilisis.</p>
  <a class="pill light" style="left:522px;top:2648px;width:161px;height:42px">Learn more</a>
</section>

<section>
  <h2 class="abs heading contact-title">Contact us</h2>
  <p class="abs contact-text">Lorem ipsum dolor sit amet, consectetur adipiscing elit, sed do eiusmod tempor incididunt ut labore et dolore magna aliqua. Quis ipsum suspendisse ultrices gravida. Risus commodo viverra maecenas accumsan lacus vel facilisis.</p>
  <div class="abs social" style="left:113px;top:3141px" aria-label="Social links"><span></span><span></span><span></span><span></span></div>

  <div class="abs field" style="top:2906px;height:66px;padding-top:24px">Name</div>
  <div class="abs field" style="top:2985px;height:66px;padding-top:24px">Email</div>
  <div class="abs field" style="top:3065px;height:138px">Message</div>
  <a class="pill light" style="left:627px;top:3235px;width:161px;height:43px">Contact us</a>
</section>

<footer class="abs site-footer">
  <div class="brand" style="position:absolute;left:0;top:92px;width:1200px;justify-content:center"><span class="brand-square"></span>LAKESIDE CNC</div>
</footer>
<nav>
  <span class="abs footer-nav" style="left:329px">Home</span>
  <span class="abs footer-nav" style="left:418px">Services we offer</span>
  <span class="abs footer-nav" style="left:580px">Capabilities</span>
  <span class="abs footer-nav" style="left:706px">About us</span>
  <span class="abs footer-nav" style="left:815px">Contact</span>
</nav>
<div class="abs social" style="left:522px;top:3615px" aria-label="Social links"><span></span><span></span><span></span><span></span></div>
<div class="abs footer-rule"></div>
<p class="abs copyright">© Copyrights 2023 Lakeside | All Rights Reserved</p>

</body>
</html>
```